Fitness Equipment & Service

I want to make the card eye catching and fun. We are called Corvane Motion Limited and we are based in Wales. We sell, install and service all types of fitness equipment from Skipping ropes, right through the Dumbbells, Kettle bells and Barbells through to state of the art Treadmills, Running Machines and Strength Equipment. We also design and install changing room furniture and lockers.

TYPOGRAPHY
We would like to use Futrura. Futura has an appearance of efficiency and forwardness. The typeface is derived
from simple geometric forms (near-perfect circles, triangles and squares) and is based on strokes of
near-even weight, which are low in contrast. This is most visible in the almost perfectly round stroke of
the o, which is nonetheless slightly ovoid.
The lowercase has tall ascenders, which rise above the cap line. The uppercase
characters present proportions similar to those of classical Roman capitals.

TYPOGRAPHIC CONSIDERATIONS
No Strike though
No Horizontal Scaling
No Drop Shadows
No Effects
Never use less than 120% Leading

OUR CORPORATE COLOURS
BRAND GUIDELINES
We were thinking that our primary colour palette consists of the Acid Green (Pantone 382) and Process Black.

We work closely with tquarly Ltd and would like to include their name on the card somewhere. I have attached images of the other brands that we work with as an idea or the small icons I have included that illustrate what we do?. I have very kindly been given permission to use any of the images off the files that I have included below, so I hope these help. I will include these below. I would be open to suggestions if it made the card more striking Can you do it?
Updates

Hi All, Just wanted to add a few thoughts but you are the guys with the creative visions (thats why are here) We are based in Wales, UK and we would be open to lots of different ideas on a theme but must be eye catching, Bold and FUN. If you can or think that the Welsh or any dragon could be put in there then go for it (its not a must have) We have also added some ideas for colour but again its over to you!! GO FOR IT ! Thanks and look forward to your visions! Owen

Hi All, Just thought I would sen through the contact details that need to be on the card. (if you want to play around with icons instead of the wording twitter, Facebook, go for it): Corvane Motion Limited Owen Pritchard Managing Director Mob: +44 (0)7582 913 406 e-mail: sales@corvanemotion.co.uk Web: Corvanemotion.co.uk twitter: @motionLetterbin Facebook: Corvane Motion Limited

```html
<!DOCTYPE html>
<html lang="en">
<head>
<meta charset="utf-8">
<title>Corvane Motion Limited – Business Card</title>
<link rel="stylesheet" href="https://fonts.googleapis.com/css2?family=Jost:wght@400;500;600&display=swap">
<style>
  :root{
    --page:#d9d4cc;
    --card:#eef0f1;
    --navy-deep:#0e1d4f;
    --navy:#20357a;
    --gold:#b8862e;
    --gold-light:#e3b25a;
    --ink:#15161a;
    --text-light:#f3f4f8;
    --title-brown:#6a4a1c;
  }
  html,body{margin:0;padding:0;overflow:hidden;}
  body{
    width:1200px;height:969px;background:var(--page);
    font-family:"Jost",sans-serif;position:relative;
  }
  .card{
    position:absolute;left:80px;top:188px;width:1040px;height:590px;
    background:var(--card);overflow:hidden;
  }
  .card-globe{position:absolute;left:0;top:0;}
  .address{
    position:absolute;left:45px;top:268px;margin:0;
    color:var(--text-light);font-size:27px;line-height:1.33;font-weight:400;
  }
  .contact-list{
    position:absolute;left:50px;top:366px;margin:0;padding:0;list-style:none;
    color:var(--text-light);font-size:26px;line-height:1.5;
  }
  .contact-list li{display:flex;align-items:center;gap:14px;height:39.5px;}
  .contact-list svg{width:22px;height:22px;flex:none;}
  .brand{
    position:absolute;right:55px;top:38px;display:flex;flex-direction:column;align-items:center;
  }
  .brand-mark{width:214px;height:214px;border-radius:50%;background:var(--navy);}
  .brand-name{
    margin:26px 0 0;font-size:34px;font-weight:600;line-height:1.2;color:var(--ink);
    text-transform:uppercase;letter-spacing:1px;text-align:center;
  }
  .person{position:absolute;right:55px;top:466px;text-align:right;}
  .person-name{margin:0;font-size:37px;font-weight:500;line-height:1.2;color:var(--ink);}
  .person-role{margin:2px 0 0;font-size:29px;font-weight:400;line-height:1.2;color:var(--title-brown);}
</style>
</head>
<body>
  <section class="card">
    <svg class="card-globe" width="1040" height="590" viewBox="0 0 1040 590" role="img" aria-label="Dark blue globe with world map and gold rim">
      <defs>
        <radialGradient id="globeFill" cx="0.45" cy="0.35" r="0.7">
          <stop offset="0" stop-color="var(--navy)"/>
          <stop offset="1" stop-color="var(--navy-deep)"/>
        </radialGradient>
      </defs>
      <circle cx="161" cy="546" r="386" fill="var(--gold)"/>
      <circle cx="161" cy="546" r="375" fill="url(#globeFill)"/>
    </svg>

    <p class="address">2219 Willowmere Road<br>Brackenford, Wales 51806</p>

    <ul class="contact-list">
      <li>
        <svg viewBox="0 0 22 22"><rect x="6" y="1.5" width="10" height="19" rx="2" fill="none" stroke="var(--text-light)" stroke-width="1.8"/><circle cx="11" cy="17" r="1.2" fill="var(--text-light)"/></svg>
        +44 (0)7582 913 406
      </li>
      <li>
        <svg viewBox="0 0 22 22"><rect x="1.5" y="5" width="19" height="13" fill="var(--text-light)"/><path d="M1.5 5 L11 12.5 L20.5 5" fill="none" stroke="var(--navy-deep)" stroke-width="1.6"/></svg>
        sales@corvanemotion.co.uk
      </li>
      <li>
        <svg viewBox="0 0 22 22"><circle cx="11" cy="11" r="9" fill="none" stroke="var(--text-light)" stroke-width="1.8"/><ellipse cx="11" cy="11" rx="4" ry="9" fill="none" stroke="var(--text-light)" stroke-width="1.4"/><line x1="2" y1="11" x2="20" y2="11" stroke="var(--text-light)" stroke-width="1.4"/></svg>
        www.Corvanemotion.co.uk
      </li>
      <li>
        <svg viewBox="0 0 22 22"><rect x="2" y="2" width="18" height="18" rx="2" fill="var(--text-light)"/></svg>
        @motionLetterbin
      </li>
      <li>
        <svg viewBox="0 0 22 22"><rect x="2" y="2" width="18" height="18" rx="2" fill="var(--text-light)"/></svg>
        Corvane Motion Limited
      </li>
    </ul>

    <div class="brand">
      <div class="brand-mark"></div>
      <p class="brand-name">Corvane Motion<br>Limited</p>
    </div>

    <div class="person">
      <p class="person-name">Owen Pritchard</p>
      <p class="person-role">Managing Director</p>
    </div>
  </section>
</body>
</html>
```